Hi,
We are also sourcing for a logo, if you have ideas please take a look at our other project (if you look at our profile you should be able to see it).
We are looking for a website that will be used to manage mobile devices. The feature set is rather small, users can Wipe, Lock, Locate devices as well as make them Ring or Speak (by sending text to be spoken). We attached some images of what it looks like right now. We are looking for simplicity, uniformity and most importantly, the website should be thought of as primary User Interface, it should flow.
Please see attached to get an idea of what it looks like now. The current design was inspired by making a site that will work and flow well on a variety of displays (from mobile to tablet to desktop).
We want to stay away from radio buttons, check-boxes. This should be engaging and creative, opposite of Corporate. Not busy (ideally we are looking to have fewest possible choices at any given time and at the same time no feature should be more than 3 clicks away (this is a suggestion/approximation... just want to share our understanding of what 'flow' is).
Could be cartoony.
Thanks!
BrisketLoom
Reason: there are a couple of designs that are interesting, in addition to specific feedback I provided, possibly looking for more concepts.
Thank You

```html
<!DOCTYPE html>
<html lang="en">
<head>
<meta charset="utf-8">
<title>BrisketLoom – Lost your phone?</title>
<link href="https://fonts.googleapis.com/css2?family=Arvo:wght@400;700&family=Arimo:wght@400&family=Kalam:wght@400&display=swap" rel="stylesheet">
<style>
  :root {
    --charcoal: #3a3a3a;
    --panel: rgba(58, 58, 58, 0.94);
    --green: #8cbf1a;
    --green-dark: #1f8a1f;
    --green-mid: #4aa821;
    --ink: #4a4a4a;
    --ink-soft: #555555;
    --mist: #e2e2e2;
    --white: #ffffff;
  }
  * { box-sizing: border-box; margin: 0; padding: 0; }
  html, body { width: 1066px; height: 1200px; overflow: hidden; background: var(--white); }
  .page { position: relative; width: 1066px; height: 1200px; font-family: "Arvo", serif; color: var(--ink); }

  .site-header { position: absolute; left: 0; top: 0; width: 1066px; height: 105px; background: var(--charcoal); }
  .brand { position: absolute; left: 66px; top: 38px; display: flex; align-items: center; gap: 8px;
    font-family: "Arvo", serif; font-size: 28px; color: var(--white); }
  .brand-dot { width: 10px; height: 10px; border-radius: 50%; background: var(--green); }

  .hero { position: absolute; left: 0; top: 105px; width: 1066px; height: 392px; }
  .hero-photo { position: absolute; inset: 0;
    background: linear-gradient(100deg, #c9362e 0%, #d8584a 22%, #e0b49a 42%, #d23c78 58%, #e9c9b2 72%, #3fa6a8 86%, #e8dccd 100%); }
  .welcome-panel { position: absolute; left: 366px; top: 171px; width: 471px; height: 203px; background: var(--panel); }
  .welcome-title { position: absolute; left: 4px; top: 28px; font-size: 36px; line-height: 36px; color: var(--white); }
  .welcome-title .name { color: var(--green); }
  .welcome-copy { position: absolute; left: 4px; top: 110px; font-size: 13.5px; line-height: 19px; color: var(--white); }
  .welcome-copy .accent { display: block; font-size: 24px; line-height: 26px; color: var(--green); }
  .store-label { position: absolute; left: 248px; top: 84px; font-family: "Arimo", sans-serif; font-size: 20px; color: var(--white); }
  .store-button { position: absolute; left: 248px; top: 114px; width: 208px; height: 55px; background: var(--white);
    display: flex; align-items: center; justify-content: center; gap: 10px;
    font-family: "Arvo", serif; font-size: 26px; color: #6a6a6a; }
  .store-square { width: 16px; height: 16px; background: var(--green); }

  .devices { position: absolute; left: 58px; top: 186px; width: 308px; height: 364px; border-radius: 34px;
    background: linear-gradient(160deg, #4a4a4a 0%, #111 55%, #2b2b2b 100%); box-shadow: 0 10px 18px rgba(0,0,0,.25); }

  .feature-band { position: absolute; left: 0; top: 497px; width: 1066px; height: 330px;
    background: linear-gradient(180deg, var(--mist) 0%, #f6f6f6 60%, var(--white) 100%); }
  .band-rule { position: absolute; left: 144px; top: 72px; width: 712px; height: 2px;
    background: linear-gradient(90deg, transparent, #ffffff 20%, #ffffff 80%, transparent); }

  .lost-heading { position: absolute; left: 170px; top: 650px; }
  .lost-heading .small { display: block; font-size: 27px; line-height: 30px; color: var(--green); }
  .lost-heading .big { font-size: 46px; line-height: 50px; font-weight: 700; color: var(--ink-soft); }
  .lost-heading .mark { font-size: 84px; font-weight: 700; color: var(--ink-soft); position: absolute; left: 136px; top: -4px; }

  .action-card { position: absolute; left: 387px; top: 601px; width: 359px; height: 177px; background: var(--white);
    box-shadow: 0 14px 10px -8px rgba(0,0,0,.28); }
  .action { position: absolute; display: flex; align-items: center; gap: 12px; font-size: 19px; color: #5a5a5a; }
  .action svg { flex: none; }

  .app-arrow { position: absolute; left: 746px; top: 629px; width: 144px; height: 128px; }
  .app-arrow-text { position: absolute; left: 766px; top: 654px; color: var(--white); font-weight: 700; line-height: 26px; }
  .app-arrow-text .line1 { display: block; font-size: 20px; }
  .app-arrow-text .line2 { display: block; font-size: 32px; }

  .thumb { position: absolute; border: 1px solid #d6d6d6; }
  .thumb-lost { left: 253px; top: 853px; width: 102px; height: 68px; background: linear-gradient(135deg, #2b3b55, #8a6a55 55%, #d9d9d9); }
  .thumb-protect { left: 543px; top: 854px; width: 103px; height: 68px; background: linear-gradient(135deg, #ffffff, #e8e4de 55%, #2a2a2a); }
  .col-title { position: absolute; font-size: 19px; color: var(--green); }
  .col-title.lost { left: 365px; top: 857px; line-height: 22px; }
  .col-title.lost .phone { display: block; font-size: 30px; line-height: 36px; font-weight: 700; color: #333; }
  .col-title.lost .phone span { color: var(--green); }
  .col-title.protect { left: 662px; top: 873px; }

  .feature-list { position: absolute; list-style: none; font-family: "Arimo", sans-serif; font-size: 10.5px; color: #444; }
  .feature-list li { position: relative; padding-left: 17px; text-decoration: underline; text-decoration-color: #888; }
  .feature-list li::before { content: ""; position: absolute; left: 0; top: 3px; width: 7px; height: 7px; background: var(--green); }
  .feature-list.lost { left: 253px; top: 952px; }
  .feature-list.lost li { height: 24.5px; }
  .feature-list.protect { left: 542px; top: 954px; }
  .feature-list.protect li { height: 25px; }
  .feature-list.protect li:nth-child(4), .feature-list.protect li:nth-child(5) { height: 28px; }

  .site-footer { position: absolute; left: 0; top: 1105px; width: 1066px; height: 95px; background: var(--charcoal);
    font-family: "Kalam", cursive; font-size: 13px; color: var(--white); }
  .copyright { position: absolute; left: 68px; top: 42px; }
  .footer-nav { position: absolute; right: 109px; top: 42px; display: flex; gap: 10px; }
</style>
</head>
<body>
<div class="page">
  <header class="site-header">
    <div class="brand"><span class="brand-dot"></span>BrisketLoom</div>
  </header>

  <section class="hero">
    <div class="hero-photo" role="img" aria-label="Photo of students in colourful shirts using a white smartphone beside books"></div>
    <div class="welcome-panel">
      <h1 class="welcome-title">Welcome to<br><span class="name">BrisketLoom</span></h1>
      <p class="welcome-copy">Find out what's happening,<br>Right Now ,with the<span class="accent">mobile device</span>you care about</p>
      <div class="store-label">Get it on</div>
      <div class="store-button"><span class="store-square"></span>Appvale</div>
    </div>
  </section>

  <section class="feature-band"><div class="band-rule"></div></section>
  <div class="devices" role="img" aria-label="Two black smartphones standing side by side"></div>

  <h2 class="lost-heading"><span class="small">Lost your</span><span class="big">Phone</span><span class="mark">?</span></h2>

  <div class="action-card">
    <div class="action" style="left:24px;top:22px;">
      <svg width="34" height="46" viewBox="0 0 34 46"><path d="M8 20V13a9 9 0 0 1 18 0v7" fill="none" stroke="#555" stroke-width="5"/><rect x="2" y="20" width="30" height="24" rx="3" fill="#5a5a5a"/><rect x="15" y="28" width="4" height="9" fill="#fff"/></svg>lock it</div>
    <div class="action" style="left:200px;top:22px;">
      <svg width="42" height="42" viewBox="0 0 42 42"><rect x="2" y="2" width="38" height="38" fill="#e8e8e8" stroke="#555" stroke-width="3"/><path d="M10 30 L20 12 L32 20 L22 32 Z" fill="#fff" stroke="#555" stroke-width="2"/><path d="M10 30 L22 32 L16 24 Z" fill="#444"/></svg>Wipe it</div>
    <div class="action" style="left:24px;top:112px;">
      <svg width="40" height="52" viewBox="0 0 40 52"><rect x="2" y="16" width="26" height="34" rx="4" fill="#666"/><rect x="6" y="20" width="18" height="11" fill="#fff"/><path d="M24 14a8 8 0 0 1 8 8M24 7a15 15 0 0 1 15 15" fill="none" stroke="#555" stroke-width="3"/></svg>Ring it</div>
    <div class="action" style="left:204px;top:118px;">
      <svg width="44" height="40" viewBox="0 0 44 40"><circle cx="16" cy="16" r="11" fill="#fff" stroke="#555" stroke-width="4"/><path d="M24 24 L40 36" stroke="#555" stroke-width="6" stroke-linecap="round"/></svg>Find it</div>
  </div>

  <svg class="app-arrow" viewBox="0 0 144 128" aria-hidden="true">
    <defs><linearGradient id="arrowFill" x1="0" y1="0" x2="0" y2="1"><stop offset="0" stop-color="#7cc12a"/><stop offset="1" stop-color="#138a1f"/></linearGradient></defs>
    <path d="M0 0 H70 L144 60 L70 128 H0 Z" fill="url(#arrowFill)"/>
  </svg>
  <div class="app-arrow-text"><span class="line1">Get the</span><span class="line2">app</span></div>

  <div class="thumb thumb-lost" role="img" aria-label="Photo of a hand pulling a phone from a jeans pocket"></div>
  <h3 class="col-title lost">Lost or Stolen<span class="phone">PHONE<span>?</span></span></h3>
  <ul class="feature-list lost">
    <li>Find your phone when need it  most by maps or ringer</li>
    <li>Remotely wipe your confidential data</li>
    <li>Register your stolen phone</li>
  </ul>

  <div class="thumb thumb-protect" role="img" aria-label="Photo of a toy bear sitting behind a black laptop"></div>
  <h3 class="col-title protect">Protect or Secure</h3>
  <ul class="feature-list protect">
    <li>Monitor instant messages through SMS</li>
    <li>Record Voice Commentaries</li>
    <li>Camera Observation</li>
    <li>Get notified your child is skipping the class</li>
    <li>Back up and share your pictures and contacts</li>
  </ul>

  <footer class="site-footer">
    <div class="copyright">©brisketloominc·2012</div>
    <nav class="footer-nav"><span>terms &amp; conditions</span><span>Frequently asked questions</span><span>about</span><span>Contact</span></nav>
  </footer>
</div>
</body>
</html>
```